Foot and ankle surgeon requires a website design

I need a website where prospective and established patients can obtain information and then direct them to making appointments. My practice is a highly professional surgical practice specialising in surgery to the foot and ankle. My title is Mr Colin Brasket, Podiatric Foot & Ankle Surgeon. My qualifications are: BSc MSc FACPS
The practice website will require information on: Locations, phone numbers to make appointments, general background on podiatric surgery,
I would like to include information on: my hospital appointments, surgical fellowships held, training programs undertaken, association memberships, publications written, links to useful websites
A page dedicated to common foot conditions would be useful and also a page with referral information including an online registration section that will be sent direct to the receptionist.
Examples of similar websites include:
http://www.dorvelquintaro.com.au/
http://www.haldenfootsurgeon.com.au/
I will provide files on logo, self photos and my personal training history etc.
Also if there is going to be a background theme I personally am associated with surfing and beach activities, it would be great if this was able to be reflected in the design.
Thank you.

```html
<!DOCTYPE html>
<html lang="en">
<head>
<meta charset="utf-8">
<title>Mr Colin Brasket – Podiatric Foot &amp; Ankle Surgeon</title>
<link rel="stylesheet" href="https://fonts.googleapis.com/css2?family=Open+Sans:wght@400;600;700&family=Arimo:wght@400;700&display=swap">
<style>
:root{
  --navy:#1f5a8e;
  --navy-dark:#174a77;
  --orange:#ee7d12;
  --ink:#2b2b2b;
  --grey:#666;
  --rule:#d9d9d9;
  --panel:#222;
  --footer:#2c2c2c;
  --footer-bottom:#262626;
  --paper:#fff;
}
*{box-sizing:border-box;margin:0;padding:0}
html,body{width:1031px;height:1200px;overflow:hidden;background:var(--paper)}
body{position:relative;font-family:"Open Sans",sans-serif;color:var(--ink)}
.abs{position:absolute}

/* header */
.brand{left:122px;top:38px;display:flex;align-items:center;gap:8px}
.brand-dot{width:14px;height:14px;border-radius:50%;background:var(--orange)}
.brand-name{font-size:15px;font-weight:700;color:var(--navy);line-height:1.15}
.brand-name small{display:block;font-size:8px;font-weight:700;color:var(--navy)}
.call{right:121px;top:29px;font-size:13px;font-weight:600;color:#333;display:flex;align-items:center;gap:6px}
.call b{font-size:16px;font-weight:600;color:#444}
.search{left:730px;top:69px;width:180px;height:21px;border:1px solid #c9c9c9;border-radius:4px;background:#f4f4f4;font-size:9px;font-style:italic;color:#999;padding:4px 10px}
.search svg{position:absolute;right:7px;top:3px}

/* navigation */
.nav{left:122px;top:112px;width:787px;height:33px;background:var(--paper);box-shadow:0 2px 5px rgba(0,0,0,.25);padding:3px}
.nav ul{list-style:none;display:flex;justify-content:space-between;align-items:center;height:27px;background:var(--navy);padding:0 4px}
.nav li{font-size:10.4px;font-weight:600;color:#fff;text-transform:uppercase}
.nav li.current{color:var(--orange)}

/* hero */
.hero{left:121px;top:152px;width:790px;height:335px;border:1px solid #ddd;padding:4px;background:#fff;box-shadow:0 6px 10px -6px rgba(0,0,0,.25)}
.hero-photo{width:100%;height:100%;background:linear-gradient(100deg,#e08a6e 0%,#e6c4ad 30%,#efd9c6 55%,#ddc3ab 100%)}
.hero-dots{left:445px;top:458px}

/* welcome */
.h2{font-size:17px;font-weight:600;color:var(--navy)}
.welcome-title{left:121px;top:514px}
.welcome-photo{left:120px;top:563px;width:195px;height:181px;border:1px solid #ddd;padding:5px;background:#fff}
.fill{width:100%;height:100%}
.welcome-photo .fill{background:linear-gradient(135deg,#b9c7d4,#d9c2ad 60%,#9aa9bb)}
.welcome-text{left:323px;top:565px;width:320px;font-size:9.6px;line-height:14.5px;color:#333;text-align:justify}
.welcome-text h3{font-size:11.5px;font-weight:400;color:#111;margin-bottom:17px;text-align:left}
.welcome-text p+p{margin-top:14px}

/* appointment panel */
.appt{left:669px;top:518px;width:241px;height:231px;background:var(--panel);border-bottom:4px solid var(--navy)}
.appt h2{height:32px;background:var(--navy);color:#fff;font-size:16.5px;font-weight:600;padding:3px 9px}
.appt form{padding:10px 9px}
.field{display:flex;justify-content:space-between;align-items:center;margin-bottom:9px}
.field label{font-family:Arimo,sans-serif;font-size:10px;font-weight:700;color:#fff}
.field span{width:160px;height:24px;background:#f2f2f2}
.field.tall{align-items:flex-start}
.field.tall label{margin-top:9px}
.field.tall span{height:45px}
.submit{margin:6px 0 0 auto;width:80px;height:24px;background:var(--orange);color:#fff;font-size:13px;text-align:center;line-height:24px}

/* about */
.about-title{left:122px;top:768px}
.about-rule{left:122px;top:797px;width:507px;height:1px;background:var(--rule)}
.about-photo{left:122px;top:811px;width:193px;height:141px;background:linear-gradient(120deg,#7ea9cf,#d3dee8 50%,#9fbad3)}
.about-text{left:322px;top:808px;width:307px;font-family:Arimo,sans-serif}
.about-text h3{font-size:14px;font-weight:400;color:var(--navy);line-height:17px;margin-bottom:13px}
.about-text p{font-size:9.4px;line-height:15.5px;color:#222;text-align:justify}

/* news */
.news-title{left:666px;top:768px}
.news-arrows{left:878px;top:776px;display:flex;gap:4px}
.news-arrows span{width:13px;height:12px;background:#c8ced6;display:flex;align-items:center;justify-content:center}
.news-rule{left:666px;width:243px;height:1px;background:var(--rule)}
.news-item{left:666px;width:243px;display:flex;gap:9px}
.news-item .thumb{width:59px;height:60px;flex:none;background:linear-gradient(#e4d6cb,#c9a894)}
.news-item p{font-family:Arimo,sans-serif;font-size:8.8px;line-height:11.7px;color:#777;text-align:justify;margin-top:7px}
.news-item a{display:block;font-family:Arimo,sans-serif;font-size:9.5px;color:#2a63c8;text-decoration:none;margin-top:7px}

/* footer */
.footer{left:0;top:989px;width:1031px;height:174px;background:var(--footer)}
.footer-bottom{left:0;top:1163px;width:1031px;height:37px;background:var(--footer-bottom);border-top:1px solid #3c3c3c;text-align:center;font-family:Arimo,sans-serif;font-size:9.5px;color:#ddd;line-height:36px}
.links{list-style:none;font-family:Arimo,sans-serif;font-size:9.6px;color:#fff}
.links li{height:24px}
.footer h4{font-size:13px;font-weight:400;color:#fff;text-transform:uppercase}
.input{width:169px;height:27px;background:#fff;font-family:Arimo,sans-serif;font-size:9.5px;color:#444;padding:6px 6px}
.signup{left:616px;top:1113px;width:76px;height:26px;background:var(--navy-dark);color:#fff;font-size:12.5px;text-align:center;line-height:26px}
.address{left:765px;top:1031px;font-family:Arimo,sans-serif;font-size:9.6px;line-height:14.5px;color:#fff}
.social{left:769px;top:1127px;display:flex;gap:6px}
.social span{width:23px;height:23px;border-radius:50%;background:#5a5a5a}
</style>
</head>
<body>

<header>
  <div class="abs brand">
    <span class="brand-dot"></span>
    <div class="brand-name">Mr Colin Brasket<small>Podiatric Foot &amp; Ankle Surgeon</small></div>
  </div>
  <div class="abs call">
    <svg width="16" height="12" viewBox="0 0 16 12" aria-hidden="true"><path d="M1 4c0-2 3-3 7-3s7 1 7 3v1h-4V3.5H5V5H1z" fill="#444"/><rect x="2" y="6" width="12" height="6" rx="1" fill="#444"/></svg>
    Call Us: <b>08 9047 2816</b>
  </div>
  <div class="abs search">Search...
    <svg width="14" height="14" viewBox="0 0 14 14" aria-hidden="true"><circle cx="5.5" cy="5.5" r="4" fill="none" stroke="#222" stroke-width="2"/><path d="M8.5 8.5l4.5 4.5" stroke="#222" stroke-width="2.5"/></svg>
  </div>
</header>

<nav class="abs nav">
  <ul>
    <li class="current">Home</li><li>Appointments</li><li>Surgical Fellowships</li><li>Training Programs</li><li>Memberships</li><li>Publications</li><li>Useful Websites</li><li>Contact Us</li>
  </ul>
</nav>

<section class="abs hero">
  <div class="hero-photo" role="img" aria-label="Close-up photo of a clinician's hands examining a patient's foot"></div>
</section>
<svg class="abs hero-dots" width="140" height="29" viewBox="0 0 140 29" aria-hidden="true">
  <path d="M10 0h120l10 29H0z" fill="var(--navy)"/>
  <circle cx="38" cy="15" r="6" fill="#1a1a1a"/><circle cx="60" cy="15" r="6" fill="#173e63"/>
  <circle cx="82" cy="15" r="6" fill="#173e63"/><circle cx="104" cy="15" r="6" fill="#173e63"/>
</svg>

<main>
  <h2 class="abs h2 welcome-title">Welcome to Our Company !</h2>
  <div class="abs welcome-photo"><div class="fill" role="img" aria-label="Photo of a couple reviewing paperwork together"></div></div>
  <div class="abs welcome-text">
    <h3>The Heel and Ankle Care Group &nbsp; exceptional service</h3>
    <p>As those unfamiliar with our services, we are a team of accredited health professionals dealing with the prevention, diagnosis, treatment and rehabilitation of medical and surgical conditions related to feet, ankles and lower limbs.</p>
    <p>The Heel and Ankle Care Group have practices based throughout regional Western Australia in Geraldton and Kalgoorlie and offer the following services; sports injuries, foot care, foot orthoses and diabeo take the right step and contact the Heel and Ankle Care Group for advice on your foot, ankle, heel or leg pain or sports injury.</p>
  </div>

  <aside class="abs appt">
    <h2>Request Appointments</h2>
    <form>
      <div class="field"><label>Name</label><span></span></div>
      <div class="field"><label>Email</label><span></span></div>
      <div class="field"><label>Phone:</label><span></span></div>
      <div class="field tall"><label>Comments</label><span></span></div>
      <div class="submit">SUBMIT</div>
    </form>
  </aside>

  <h2 class="abs h2 about-title">About Colin Brasket</h2>
  <div class="abs about-rule"></div>
  <div class="abs about-photo" role="img" aria-label="Photo of doctors showing an X-ray to a young patient"></div>
  <div class="abs about-text">
    <h3>The Heel and Ankle Care Group are a regional podiatry practice, comprising of a team of highly motivated health professionals</h3>
    <p>Mira Dellant is the practice principal of Heel &amp; Ankle Care Group. She finished her degree from Westbrook University in 2005 and started work in Geraldton the following year. Being a country girl at heart, Mira is pas enjoyed. While Mira's specific interests are in biomechanics, sports iall she isn't at work Mira is kept very busy by her 2 year old daughter!</p>
  </div>

  <h2 class="abs h2 news-title">News</h2>
  <div class="abs news-arrows">
    <span><svg width="6" height="8" viewBox="0 0 6 8"><path d="M5 0L0 4l5 4z" fill="#1f3f66"/></svg></span>
    <span><svg width="6" height="8" viewBox="0 0 6 8"><path d="M1 0l5 4-5 4z" fill="#1f3f66"/></svg></span>
  </div>
  <div class="abs news-rule" style="top:798px"></div>
  <div class="abs news-item" style="top:812px">
    <div class="thumb" role="img" aria-label="Portrait photo of Mira Dellant"></div>
    <div><p>Mira Dellant is the practice principal of Westbrook University in 2005 and started work in Geraldton the following year.</p><a>Mira Dellant</a></div>
  </div>
  <div class="abs news-rule" style="top:882px"></div>
  <div class="abs news-item" style="top:889px">
    <div class="thumb" role="img" aria-label="Portrait photo of Tessa Varnel"></div>
    <div><p>Mira Dellant is the practice principal of Westbrook University in 2005 and started work in Geraldton the following year.</p><a>Tessa Varnel</a></div>
  </div>
  <div class="abs news-rule" style="top:956px"></div>
</main>

<footer>
  <div class="abs footer"></div>
  <ul class="abs links" style="left:123px;top:1008px"><li>Home</li><li>About</li><li>News</li><li>Services</li><li>What We Do</li><li>Contact Us</li></ul>
  <ul class="abs links" style="left:239px;top:1008px"><li>Grief &amp; Healing</li><li>Resources</li><li>Plan Now</li><li>Locations</li><li>Privacy Policy</li><li>Terms &amp; Conditions</li></ul>
  <ul class="abs links" style="left:380px;top:1008px"><li>Resources</li><li>Plan Now</li><li>Locations</li><li>Privacy Policy</li><li>Terms &amp; Conditions</li></ul>
  <h4 class="abs" style="left:524px;top:1004px">Newsletter Sign Up</h4>
  <div class="abs input" style="left:523px;top:1036px">Enter Name</div>
  <div class="abs input" style="left:523px;top:1073px">Enter Email Address</div>
  <div class="abs signup">SIGN UP</div>
  <h4 class="abs" style="left:765px;top:1006px">Our Locations</h4>
  <address class="abs address" style="font-style:normal">Geraldton<br>48 Seabreak Drive,<br>PO BOX 7260,<br>Geraldton WA 6532<br>Ph: 08 9921 3087<br>Fax: 08 9921 3088</address>
  <div class="abs social" aria-label="Social media links"><span></span><span></span><span></span><span></span><span></span></div>
  <div class="abs footer-bottom">© Copyright &nbsp;2014 Colin Brasket All right received</div>
</footer>

</body>
</html>
```